UI/ UX Design for ERP Software

We need a new UX/UI interface for a ERP software for property managers. Our CMMS / ERP solution is made based on responsive design technologies and is coded in PHP.
The overall UX to be similar to Tev Ulna - easy navigation, intuitive menus.

Industry/Entity Type

Property Management

Number of Pages Required

5+ page

Requirements
Must have
• Round dock buttons
Consistent icons across the application
Enough Spacing between buttons/icons/ menu
Consistent Font
Nice to have
• We would like the UX to allow the users to use the application without /minimum training.
Should not have
• we don't want anything that is classic with respect to UX

```html
<!DOCTYPE html>
<html lang="en">
<head>
<meta charset="utf-8">
<title>Lotra – Active Dashboard</title>
<link href="https://fonts.googleapis.com/css2?family=Raleway:wght@400;500;600;700&display=swap" rel="stylesheet">
<style>
  :root{
    --blue:#0a84ff;
    --blue-side:#1a87f5;
    --header-bg:#eef7fd;
    --tab-bg:#dff2fc;
    --bar-bg:#516378;
    --ink:#2b3440;
    --muted:#55606c;
    --grid:#d9dde2;
    --white:#ffffff;
  }
  *{box-sizing:border-box;margin:0;padding:0}
  html,body{width:1200px;height:689px;overflow:hidden;background:var(--white);font-family:'Raleway',sans-serif;color:var(--ink)}
  .app{position:relative;width:1200px;height:689px}
  .topbar{position:absolute;left:0;top:0;width:1200px;height:59px;background:var(--header-bg)}
  .brand{position:absolute;left:22px;top:16px;display:flex;align-items:center;gap:6px;font-size:22px;font-weight:700;color:var(--blue)}
  .brand-mark{width:14px;height:14px;background:var(--blue)}
  .page-tab{position:absolute;left:137px;top:0;width:192px;height:59px;background:var(--tab-bg);display:flex;align-items:center;padding-left:17px;gap:9px;font-size:16px;font-weight:500;color:var(--ink)}
  .stat{position:absolute;top:8px;height:42px;display:flex;align-items:center}
  .stat-icon{width:42px;height:42px;background:var(--blue);display:flex;align-items:center;justify-content:center}
  .stat-text{margin-left:8px;line-height:1.1}
  .stat-value{font-size:15px;font-weight:700;color:var(--ink)}
  .stat-label{font-size:10px;color:var(--muted)}
  .menu-toggle{position:absolute;left:1162px;top:19px}
  .sidebar{position:absolute;left:1143px;top:52px;width:57px;height:637px;background:var(--blue-side)}
  .sidebar::before{content:"";position:absolute;left:23px;top:-7px;border:5px solid transparent;border-bottom:7px solid var(--blue-side);border-top:0}
  .sidebar svg{position:absolute;left:18px}
  .range-bar{position:absolute;left:26px;top:78px;width:1088px;height:37px;background:var(--bar-bg)}
  .range-tab{position:absolute;top:78px;height:37px;display:flex;align-items:center;gap:5px;font-size:10px;color:var(--white)}
  .range-tab.active{top:70px;height:46px;padding:0 15px;background:linear-gradient(180deg,#06bdf8,#0a84ff)}
  .period{position:absolute;left:30px;top:131px;display:flex;align-items:flex-end;gap:6px;font-size:16px;color:var(--ink)}
  .chart{position:absolute;left:0;top:0}
  .legend{position:absolute;font-size:9px;color:var(--muted);display:flex;align-items:center;gap:7px}
  .swatch{width:17px;height:10px;border-radius:5px}
  .page-code{position:absolute;left:1118px;top:649px;font-size:8px;color:var(--muted)}
</style>
</head>
<body>
<div class="app">
  <header class="topbar">
    <div class="brand"><span class="brand-mark"></span>Lotra</div>
    <div class="page-tab">
      <svg width="20" height="18" viewBox="0 0 20 18"><path d="M10 1 1 9h3v8h4v-5h4v5h4V9h3z" fill="#2b3440"/></svg>
      Active Dashboard
    </div>

    <div class="stat" style="left:351px">
      <div class="stat-icon"><svg width="22" height="20" viewBox="0 0 20 18"><path d="M10 1 1 9h3v8h4v-5h4v5h4V9h3z" fill="#fff"/></svg></div>
      <div class="stat-text"><div class="stat-value">03</div><div class="stat-label">Properties</div></div>
    </div>
    <div class="stat" style="left:462px">
      <div class="stat-icon"><svg width="24" height="18" viewBox="0 0 24 18"><circle cx="12" cy="5" r="3.5" fill="#fff"/><circle cx="5" cy="6" r="2.5" fill="#fff"/><circle cx="19" cy="6" r="2.5" fill="#fff"/><path d="M5 17c0-5 3-7 7-7s7 2 7 7zM0 15c0-3 2-5 5-5l-1 5zM24 15c0-3-2-5-5-5l1 5z" fill="#fff"/></svg></div>
      <div class="stat-text"><div class="stat-value">08</div><div class="stat-label">Tenants</div></div>
    </div>
    <div class="stat" style="left:559px">
      <div class="stat-icon"><svg width="22" height="22" viewBox="0 0 22 22"><path d="M11 1 7 5h3v5H5V7l-4 4 4 4v-3h5v5H7l4 4 4-4h-3v-5h5v3l4-4-4-4v3h-5V5h3z" fill="#fff"/></svg></div>
      <div class="stat-text"><div class="stat-value">422,000,00.sq.ft</div><div class="stat-label">Total Properties Area</div></div>
    </div>
    <div class="stat" style="left:737px">
      <div class="stat-icon"><svg width="22" height="22" viewBox="0 0 22 22"><path d="M11 1 7 5h3v5H5V7l-4 4 4 4v-3h5v5H7l4 4 4-4h-3v-5h5v3l4-4-4-4v3h-5V5h3z" fill="#fff"/></svg></div>
      <div class="stat-text"><div class="stat-value">233,500.00.sq.ft</div><div class="stat-label">Rented Area</div></div>
    </div>
    <div class="stat" style="left:915px">
      <div class="stat-icon"><svg width="22" height="22" viewBox="0 0 22 22"><path d="M11 1 7 5h3v5H5V7l-4 4 4 4v-3h5v5H7l4 4 4-4h-3v-5h5v3l4-4-4-4v3h-5V5h3z" fill="#fff"/></svg></div>
      <div class="stat-text"><div class="stat-value">188,500.00sq.ft</div><div class="stat-label">Vacancies Area</div></div>
    </div>

    <svg class="menu-toggle" width="20" height="15" viewBox="0 0 20 15"><rect y="0" width="20" height="2" fill="#0a84ff"/><rect y="6" width="20" height="2" fill="#0a84ff"/><rect y="12" width="20" height="2" fill="#0a84ff"/></svg>
  </header>

  <nav class="sidebar" aria-label="Main navigation">
    <svg style="top:13px" width="14" height="12" viewBox="0 0 14 12"><path d="M7 1a6 6 0 0 0-6 6v4h12V7a6 6 0 0 0-6-6zm0 9 2-5" fill="#fff" stroke="#1a87f5"/></svg>
    <svg style="top:41px" width="14" height="10" viewBox="0 0 14 10"><circle cx="7" cy="3" r="2.5" fill="#fff"/><circle cx="2.5" cy="4" r="1.8" fill="#fff"/><circle cx="11.5" cy="4" r="1.8" fill="#fff"/><rect x="1" y="6" width="12" height="4" rx="2" fill="#fff"/></svg>
    <svg style="top:68px" width="14" height="12" viewBox="0 0 14 12"><path d="M7 1 2 11M7 1l5 10M3 7h8" stroke="#fff" stroke-width="2" fill="none"/></svg>
    <svg style="top:96px" width="14" height="13" viewBox="0 0 14 13"><circle cx="7" cy="4" r="3.5" fill="#fff"/><rect x="1" y="8" width="12" height="5" rx="2.5" fill="#fff"/></svg>
    <svg style="top:124px" width="14" height="12" viewBox="0 0 14 12"><circle cx="5" cy="6" r="4" fill="#fff"/><circle cx="11" cy="3" r="2.5" fill="#fff"/><circle cx="11" cy="9" r="2.5" fill="#fff"/></svg>
    <svg style="top:152px" width="14" height="10" viewBox="0 0 14 10"><circle cx="7" cy="3" r="2.5" fill="#fff"/><circle cx="2.5" cy="4" r="1.8" fill="#fff"/><circle cx="11.5" cy="4" r="1.8" fill="#fff"/><rect x="1" y="6" width="12" height="4" rx="2" fill="#fff"/></svg>
    <svg style="top:179px" width="14" height="13" viewBox="0 0 14 13"><path d="M3 0h6l3 3v10H3z" fill="#fff"/></svg>
    <svg style="top:207px" width="14" height="13" viewBox="0 0 14 13"><path d="M1 1l12 11M13 1 1 12" stroke="#fff" stroke-width="2.5"/></svg>
    <svg style="top:235px" width="14" height="14" viewBox="0 0 14 14"><circle cx="7" cy="7" r="5" fill="#fff"/><circle cx="7" cy="7" r="2" fill="#1a87f5"/></svg>
    <svg style="top:263px" width="14" height="12" viewBox="0 0 14 12"><path d="M4 2 0 6l4 4M10 2l4 4-4 4M8 0 6 12" stroke="#fff" stroke-width="2" fill="none"/></svg>
    <svg style="top:291px" width="14" height="14" viewBox="0 0 14 14"><circle cx="6" cy="6" r="4" stroke="#fff" stroke-width="2.2" fill="none"/><path d="M9 9l4 4" stroke="#fff" stroke-width="2.5"/></svg>
    <svg style="top:319px" width="14" height="13" viewBox="0 0 14 13"><rect x="2" y="1" width="10" height="11" fill="#fff"/><path d="M5 9V6M7 9V4M9 9V7" stroke="#1a87f5" stroke-width="1.2"/></svg>
    <svg style="top:347px" width="14" height="13" viewBox="0 0 14 13"><path d="M7 0 14 13H0z" fill="#fff"/><rect x="6.3" y="4" width="1.4" height="5" fill="#1a87f5"/></svg>
    <svg style="top:375px" width="14" height="13" viewBox="0 0 14 13"><rect y="0" width="14" height="3" fill="#fff"/><rect y="5" width="14" height="3" fill="#fff"/><rect y="10" width="14" height="3" fill="#fff"/></svg>
    <svg style="top:403px" width="15" height="11" viewBox="0 0 15 11"><rect width="15" height="11" fill="#fff"/><circle cx="7.5" cy="5.5" r="2.5" fill="#1a87f5"/></svg>
    <svg style="top:431px" width="15" height="12" viewBox="0 0 15 12"><ellipse cx="6" cy="5" rx="6" ry="4.5" fill="#fff"/><ellipse cx="10" cy="8" rx="5" ry="3.5" fill="#fff"/></svg>
    <svg style="top:458px" width="14" height="14" viewBox="0 0 14 14"><path d="M3 0h8v14H3z" fill="#fff"/><path d="M5 5h4M5 8h4" stroke="#1a87f5"/></svg>
    <svg style="top:486px" width="14" height="12" viewBox="0 0 14 12"><path d="M1 1v10h12" stroke="#fff" stroke-width="1.5" fill="none"/><path d="M4 9V5M7 9V3M10 9V6" stroke="#fff" stroke-width="2"/></svg>
    <svg style="top:514px" width="14" height="14" viewBox="0 0 14 14"><path d="M3 0h6l3 3v11H3z" fill="#fff"/><path d="M5 7h5M5 10h5" stroke="#1a87f5"/></svg>
    <svg style="top:542px" width="14" height="14" viewBox="0 0 14 14"><path d="M3 0h6l3 3v11H3z" fill="#fff"/><rect x="6" y="5" width="2" height="6" fill="#1a87f5"/></svg>
    <svg style="top:570px" width="14" height="12" viewBox="0 0 14 12"><circle cx="5" cy="6" r="4" fill="#fff"/><circle cx="11" cy="3" r="2.5" fill="#fff"/><circle cx="11" cy="9" r="2.5" fill="#fff"/></svg>
    <svg style="top:598px" width="14" height="14" viewBox="0 0 14 14"><path d="M2 12l6-6" stroke="#fff" stroke-width="3"/><circle cx="10" cy="4" r="3.5" fill="#fff"/></svg>
  </nav>

  <div class="range-bar"></div>
  <div class="range-tab active" style="left:511px">
    <svg width="12" height="12" viewBox="0 0 12 12"><circle cx="6" cy="6" r="5" stroke="#fff" stroke-width="1.3" fill="none"/><path d="M6 3v3l2 1.5" stroke="#fff" stroke-width="1.2" fill="none"/></svg>Last 7 days</div>
  <div class="range-tab" style="left:622px"><svg width="12" height="12" viewBox="0 0 12 12"><circle cx="6" cy="6" r="5" stroke="#fff" stroke-width="1.3" fill="none"/><path d="M6 3v3l2 1.5" stroke="#fff" stroke-width="1.2" fill="none"/></svg>Last months</div>
  <div class="range-tab" style="left:713px"><svg width="12" height="12" viewBox="0 0 12 12"><circle cx="6" cy="6" r="5" stroke="#fff" stroke-width="1.3" fill="none"/><path d="M6 3v3l2 1.5" stroke="#fff" stroke-width="1.2" fill="none"/></svg>Last 3 months</div>
  <div class="range-tab" style="left:817px"><svg width="12" height="12" viewBox="0 0 12 12"><circle cx="6" cy="6" r="5" stroke="#fff" stroke-width="1.3" fill="none"/><path d="M6 3v3l2 1.5" stroke="#fff" stroke-width="1.2" fill="none"/></svg>Next 7 days</div>
  <div class="range-tab" style="left:910px"><svg width="12" height="12" viewBox="0 0 12 12"><circle cx="6" cy="6" r="5" stroke="#fff" stroke-width="1.3" fill="none"/><path d="M6 3v3l2 1.5" stroke="#fff" stroke-width="1.2" fill="none"/></svg>Next months</div>
  <div class="range-tab" style="left:1006px"><svg width="12" height="12" viewBox="0 0 12 12"><circle cx="6" cy="6" r="5" stroke="#fff" stroke-width="1.3" fill="none"/><path d="M6 3v3l2 1.5" stroke="#fff" stroke-width="1.2" fill="none"/></svg>Next 3 months</div>

  <div class="period">
    <svg width="20" height="20" viewBox="0 0 20 20"><rect x="0" y="10" width="5" height="10" fill="#516378"/><rect x="7" y="0" width="5" height="20" fill="#516378"/><rect x="14" y="6" width="6" height="14" fill="#516378"/></svg>
    <span>12/27/2020 &nbsp;- &nbsp;01/03/2021</span>
  </div>

  <svg class="chart" width="1140" height="500" viewBox="0 0 1140 500" font-family="Raleway, sans-serif">
    <g fill="#516378"><rect x="31" y="181" width="15" height="2"/><rect x="31" y="186.5" width="15" height="2"/><rect x="31" y="192" width="15" height="2"/></g>
    <g stroke="#d9dde2" stroke-width="0.8">
      <line x1="96" y1="193" x2="1107" y2="193"/>
      <line x1="96" y1="246" x2="1107" y2="246"/>
      <line x1="96" y1="297" x2="1107" y2="297"/>
      <line x1="96" y1="351" x2="1107" y2="351"/>
      <line x1="96" y1="404" x2="1107" y2="404"/>
    </g>
    <line x1="96" y1="457" x2="1107" y2="457" stroke="#9aa3ad" stroke-width="0.8"/>
    <g stroke="#9aa3ad" stroke-width="0.8">
      <line x1="96" y1="457" x2="96" y2="468"/><line x1="222" y1="457" x2="222" y2="468"/><line x1="348" y1="457" x2="348" y2="468"/><line x1="475" y1="457" x2="475" y2="468"/><line x1="601" y1="457" x2="601" y2="468"/><line x1="728" y1="457" x2="728" y2="468"/><line x1="854" y1="457" x2="854" y2="468"/><line x1="980" y1="457" x2="980" y2="468"/><line x1="1106" y1="457" x2="1106" y2="468"/>
    </g>
    <g font-size="11" fill="#2b3440" text-anchor="end">
      <text x="83" y="194">1.25</text><text x="80" y="247">1</text><text x="80" y="298">0.75</text><text x="80" y="352">0.5</text><text x="80" y="405">0.25</text><text x="80" y="458">0</text>
    </g>
    <text x="45" y="340" font-size="11" fill="#55606c" text-anchor="middle" transform="rotate(-90 45 340)">Number</text>
    <g font-size="8" fill="#55606c" text-anchor="middle">
      <text x="158" y="474">12/27/2020</text><text x="283" y="474">12/28/2020</text><text x="408" y="474">12/29/2020</text><text x="538" y="474">12/30/2020</text><text x="664" y="474">12/31/2020</text><text x="790" y="474">01/01/2021</text><text x="912" y="474">01/02/2021</text><text x="1042" y="474">01/03/2021</text>
    </g>
    <rect x="516" y="246" width="3.5" height="210" rx="1.5" fill="#0a7bff"/>
  </svg>

  <div class="legend" style="left:85px;top:529px"><span class="swatch" style="background:#0a7bff"></span>Scheduled Maintenance</div>
  <div class="legend" style="left:85px;top:559px"><span class="swatch" style="background:#8ee07a"></span>Completed Scheduled Maintenance</div>
  <div class="legend" style="left:85px;top:589px"><span class="swatch" style="background:#f7a050"></span>Future Scheduled Maintenance</div>
  <div class="legend" style="left:413px;top:529px"><span class="swatch" style="background:#3d3f45"></span>Scheduled Work Orders</div>
  <div class="legend" style="left:413px;top:560px"><span class="swatch" style="background:#8886e0"></span>Completed Work Orders</div>
  <div class="legend" style="left:697px;top:529px"><span class="swatch" style="background:#ef5b80"></span>Property Inspections in Progress</div>
  <div class="legend" style="left:699px;top:560px"><span class="swatch" style="background:#e3d252"></span>Completed Property Inspections</div>

  <div class="page-code">M1</div>
</div>
</body>
</html>
```